Business Card Design

We are looking for a business card designed for our landscaping company. We do landscaping installation & Maintenance Services. We would like to see designs that have basic landscaping in background. We also think it is important to have both of our names and phone numbers on the card. We need something that stands out a little whether it is shape of the card or thickness or design.

Business

Bramblewood Yardworks, bramblewoodyard@mailvista.net, Owen Platt 555-273-9104, Daniel Korbin 555-618-3927

```html
<!DOCTYPE html>
<html lang="en">
<head>
<meta charset="utf-8">
<title>Bramblewood Yardworks – Business Card</title>
<link rel="stylesheet" href="https://fonts.googleapis.com/css2?family=Open+Sans:wght@400;700&display=swap">
<style>
  :root {
    --backdrop: #e6e6e4;
    --leaf-green: #8cc63f;
    --ink-black: #060708;
    --card-shadow: rgba(0, 0, 0, 0.22);
  }
  html, body {
    margin: 0;
    padding: 0;
    width: 1200px;
    height: 898px;
    overflow: hidden;
    background: var(--backdrop);
    font-family: "Open Sans", Arial, sans-serif;
  }
  .business-card {
    position: absolute;
    left: 100px;
    top: 163px;
    width: 1000px;
    height: 572px;
    box-shadow: 0 14px 34px var(--card-shadow);
    overflow: hidden;
  }
  .card-art {
    position: absolute;
    inset: 0;
    width: 1000px;
    height: 572px;
    display: block;
  }
  .company-name {
    position: absolute;
    left: 104px;
    top: 128px;
    margin: 0;
    font-size: 34px;
    line-height: 46px;
    font-weight: 700;
    color: var(--leaf-green);
    letter-spacing: 0.3px;
    white-space: nowrap;
  }
  .company-email {
    position: absolute;
    left: 106px;
    top: 190px;
    display: flex;
    align-items: center;
    gap: 10px;
    font-size: 22px;
    color: var(--leaf-green);
    white-space: nowrap;
  }
  .contact-list {
    position: absolute;
    left: 640px;
    top: 190px;
    margin: 0;
    padding: 0;
    list-style: none;
    color: var(--ink-black);
  }
  .contact {
    margin-bottom: 40px;
  }
  .contact:nth-child(2) {
    margin-left: 40px;
  }
  .contact-name {
    display: block;
    font-size: 28px;
    font-weight: 700;
    line-height: 1.2;
    white-space: nowrap;
  }
  .contact-phone {
    display: flex;
    align-items: center;
    gap: 10px;
    margin-left: 18px;
    font-size: 27px;
    font-weight: 700;
    line-height: 1.3;
    white-space: nowrap;
  }
</style>
</head>
<body>
  <article class="business-card">
    <svg class="card-art" viewBox="0 0 1000 572" xmlns="http://www.w3.org/2000/svg">
      <defs>
        <linearGradient id="plantTone" x1="0" y1="0" x2="0" y2="1">
          <stop offset="0" stop-color="#8cc63f" stop-opacity="0.55"/>
          <stop offset="1" stop-color="#8cc63f"/>
        </linearGradient>
        <filter id="curveShadow" x="-10%" y="-10%" width="130%" height="130%">
          <feDropShadow dx="8" dy="6" stdDeviation="10" flood-color="#000" flood-opacity="0.45"/>
        </filter>
      </defs>
      <rect class="card-base" width="1000" height="572" fill="var(--leaf-green)"/>
      <path class="dark-panel" filter="url(#curveShadow)" fill="var(--ink-black)"
            d="M0,0 H650 C720,0 725,55 695,105 C610,250 390,300 372,572 H0 Z"/>
      <path class="name-swoosh" fill="var(--leaf-green)"
            d="M70,262 C20,230 20,150 120,112 C200,85 350,80 470,88 C330,90 160,100 95,140 C55,165 50,215 70,262 Z"/>
      <path class="contact-swoosh" fill="var(--ink-black)"
            d="M520,500 C720,530 955,480 985,350 C992,300 958,262 905,248 C955,290 955,420 770,480 C690,505 600,506 520,500 Z"/>
      <rect class="plant-placeholder" role="img" aria-label="Silhouette of grass and a tall reed plant"
            x="92" y="370" width="150" height="202" rx="6" fill="url(#plantTone)"/>
    </svg>

    <h1 class="company-name">Bramblewood Yardworks</h1>
    <div class="company-email">
      <svg width="22" height="22" viewBox="0 0 22 22" aria-hidden="true">
        <circle cx="11" cy="11" r="10" fill="var(--leaf-green)"/>
        <rect x="5" y="7" width="12" height="8" fill="var(--ink-black)"/>
        <path d="M5,7 L11,12 L17,7" fill="none" stroke="var(--leaf-green)" stroke-width="1.4"/>
      </svg>
      <span>bramblewoodyard@mailvista.net</span>
    </div>

    <ul class="contact-list">
      <li class="contact">
        <span class="contact-name">Owen Platt</span>
        <span class="contact-phone">
          <svg width="26" height="26" viewBox="0 0 26 26" aria-hidden="true">
            <circle cx="13" cy="13" r="11.5" fill="none" stroke="var(--ink-black)" stroke-width="2.2"/>
            <path d="M9,7 C7,8 7,11 9,14 C11,17 14,19 16,19 C18,19 19,17.5 18.5,16.5 L16.5,15 L15,16 C13.5,15.5 11,13 10.5,11.5 L11.5,10 L10.5,7.5 Z" fill="var(--ink-black)"/>
          </svg>
          555-273-9104
        </span>
      </li>
      <li class="contact">
        <span class="contact-name">Daniel Korbin</span>
        <span class="contact-phone">
          <svg width="26" height="26" viewBox="0 0 26 26" aria-hidden="true">
            <circle cx="13" cy="13" r="11.5" fill="none" stroke="var(--ink-black)" stroke-width="2.2"/>
            <path d="M9,7 C7,8 7,11 9,14 C11,17 14,19 16,19 C18,19 19,17.5 18.5,16.5 L16.5,15 L15,16 C13.5,15.5 11,13 10.5,11.5 L11.5,10 L10.5,7.5 Z" fill="var(--ink-black)"/>
          </svg>
          555-618-3927
        </span>
      </li>
    </ul>
  </article>
</body>
</html>
```